Investor Slide Deck

Simple idea - take a model investor deck and build out a investor deck for K7V. I will complete the data, I need a template to work from within. I will attach a model investor deck and a blank K7V that I need built out to K7V. Use the K7V Pwrpt to build out the investor deck

```html
<!DOCTYPE html>
<html lang="en">
<head>
<meta charset="utf-8">
<title>K7V Investor Deck</title>
<link href="https://fonts.googleapis.com/css2?family=Jost:wght@500;600;700&family=Roboto:wght@400;500;700&display=swap" rel="stylesheet">
<style>
:root{
  --stage:#58585a;
  --navy:#0d3140;
  --magenta:#a8124f;
  --orange:#ff5a0a;
  --yellow:#f5b82a;
  --blue:#1f6b85;
  --teal:#15ab9e;
  --ink:#222;
  --body:#555;
  --white:#fff;
}
*{box-sizing:border-box;margin:0;padding:0}
html,body{width:1021px;height:1200px;overflow:hidden;background:var(--stage)}
.canvas{position:relative;width:1021px;height:1200px;overflow:hidden;background:var(--stage);font-family:"Roboto",sans-serif}
.slide{position:absolute;width:795px;height:447px;background:var(--white);transform:scale(.5788);transform-origin:0 0;overflow:hidden}
.col-a{left:32px}.col-b{left:529px}
.row-1{top:34px}.row-2{top:325px}.row-3{top:616px}.row-4{top:908px}
.abs{position:absolute}
.slide-title{position:absolute;left:44px;top:20px;font-family:"Jost",sans-serif;font-weight:700;font-size:30px;letter-spacing:.5px;color:var(--ink);text-transform:uppercase}
.title-rule{position:absolute;left:0;top:66px;width:270px;height:2px;background:var(--magenta)}
.slide-footer{position:absolute;left:0;top:421px;width:795px;height:26px;background:var(--navy);color:var(--white);font-size:8px}
.slide-footer .copy{position:absolute;left:44px;top:9px}
.slide-footer .page{position:absolute;left:662px;top:0;width:133px;height:26px;background:var(--magenta);font-weight:700;text-align:center;line-height:26px}
.photo{position:absolute;overflow:hidden}
.round{border-radius:50%}
.body-text{font-size:10.5px;line-height:21px;color:var(--body);text-align:justify}
.bullet{position:absolute;display:flex;gap:12px;font-size:10.5px;line-height:21px;color:var(--body);text-align:justify}
.bullet svg{flex:none;margin-top:5px}
/* cover */
.brand{position:absolute;left:405px;top:274px;font-family:"Jost",sans-serif;font-weight:600;font-size:27px;color:var(--navy);letter-spacing:.5px;white-space:nowrap}
.date-pill{position:absolute;left:603px;top:322px;width:145px;height:31px;border-radius:16px;background:var(--magenta);color:var(--white);font-family:"Jost",sans-serif;font-weight:600;font-size:11px;text-align:center;line-height:31px}
/* services */
.service h3{font-family:"Jost",sans-serif;font-weight:600;font-size:11.5px;color:var(--ink);letter-spacing:.3px;margin-bottom:6px}
.service p{font-size:9.5px;line-height:18px;color:var(--body)}
.service{position:absolute;width:300px}
.icon-dot{position:absolute;width:64px;height:64px;border-radius:50%;display:flex;align-items:center;justify-content:center}
/* advantage */
.adv{position:absolute;width:200px;text-align:center}
.adv .ring{width:106px;height:106px;margin:0 auto;border-radius:50%;display:flex;align-items:center;justify-content:center}
.adv .ring span{width:92px;height:92px;border-radius:50%;background:var(--white);box-shadow:0 3px 8px rgba(0,0,0,.15);display:flex;align-items:center;justify-content:center}
.adv h3{margin-top:26px;font-family:"Roboto",sans-serif;font-weight:700;font-size:10.5px;letter-spacing:.2px}
.adv p{margin-top:6px;font-size:10px;line-height:21px;color:var(--body)}
/* exit */
.step{position:absolute;left:436px;width:302px;height:70px;border-radius:35px;background:var(--white);box-shadow:0 4px 14px rgba(0,0,0,.1)}
.step .dot{position:absolute;left:6px;top:6px;width:58px;height:58px;border-radius:50%;display:flex;align-items:center;justify-content:center}
.step b{position:absolute;left:82px;top:17px;font-size:10.5px;color:var(--magenta)}
.step em{position:absolute;left:82px;top:38px;font-style:normal;font-size:10px;color:var(--body)}
/* intro */
.sub-head{font-family:"Jost",sans-serif;font-weight:700;font-size:12.5px;color:var(--magenta);margin:9px 0 3px}
.strong{font-weight:700;color:var(--ink)}
.chart-label{font-family:"Jost",sans-serif;font-weight:600;fill:var(--white)}
</style>
</head>
<body>
<div class="canvas">

  <!-- Cover -->
  <section class="slide col-a row-1">
    <div class="photo round" style="left:-60px;top:-53px;width:352px;height:352px;background:linear-gradient(160deg,#8fb4d8 0%,#5d7aa0 38%,#2c3f62 62%,#6b6a42 100%)" role="img" aria-label="Engineer in safety vest inspecting rows of solar panels"></div>
    <svg class="abs" style="left:0;top:0" width="795" height="447" viewBox="0 0 795 447">
      <circle cx="116" cy="125" r="258" fill="none" stroke="var(--navy)" stroke-width="2.5" transform="translate(0,0)" clip-path="url(#none)"/>
      <line x1="442" y1="127" x2="575" y2="2" stroke="var(--orange)" stroke-width="9" stroke-linecap="round"/>
      <line x1="495" y1="99" x2="598" y2="0" stroke="var(--yellow)" stroke-width="1.5"/>
      <line x1="620" y1="437" x2="680" y2="385" stroke="#eef2ea" stroke-width="9" stroke-linecap="round"/>
      <line x1="660" y1="447" x2="740" y2="378" stroke="#eef2ea" stroke-width="1.5"/>
    </svg>
    <div class="photo round" style="left:685px;top:0;width:225px;height:225px;background:linear-gradient(120deg,#4a6b3a,#1e2c4f 55%,#6c8bb0)" role="img" aria-label="Close view of solar panels in a green field"></div>
    <svg class="abs" style="left:0;top:0" width="795" height="447"><circle cx="798" cy="112" r="119" fill="none" stroke="var(--teal)" stroke-width="1.5"/></svg>
    <div class="photo round" style="left:205px;top:342px;width:225px;height:225px;background:linear-gradient(180deg,#f3b35a 0%,#d98a3a 30%,#34476e 60%,#1c2a48 100%)" role="img" aria-label="Solar panels at sunset"></div>
    <svg class="abs" style="left:0;top:0" width="795" height="447"><circle cx="340" cy="465" r="118" fill="none" stroke="var(--orange)" stroke-width="1.5"/></svg>
    <div class="brand">K7V &nbsp;KESTREL VOLT</div>
    <div class="date-pill">Date: 10/09/2024</div>
  </section>

  <!-- Traction -->
  <section class="slide col-b row-1">
    <h2 class="slide-title">Our Traction</h2><div class="title-rule"></div>
    <div class="photo" style="left:45px;top:100px;width:217px;height:121px;border-radius:14px;background:linear-gradient(180deg,#6fa5de 0%,#bcd6ee 35%,#3c7a3a 55%,#2c3a5e 100%)" role="img" aria-label="Solar farm under a blue sky"></div>
    <div class="photo" style="left:45px;top:233px;width:217px;height:154px;border-radius:14px;background:linear-gradient(180deg,#a9cbee 0%,#7fa9d6 45%,#2d4f86 100%)" role="img" aria-label="Technicians installing a solar panel"></div>
    <div class="photo" style="left:280px;top:100px;width:229px;height:287px;border-radius:14px;background:linear-gradient(180deg,#e8e6e4 0%,#d9b68c 40%,#a4603d 75%,#6e3a24 100%)" role="img" aria-label="Two workers carrying a solar panel on a tiled roof"></div>
    <div class="photo" style="left:520px;top:100px;width:229px;height:154px;border-radius:14px;background:linear-gradient(180deg,#2f68b8 0%,#f1d67b 40%,#5f7f3a 60%,#243a72 100%)" role="img" aria-label="Solar panels with the sun rising behind"></div>
    <div class="photo" style="left:520px;top:265px;width:229px;height:122px;border-radius:14px;background:linear-gradient(90deg,#a0532e 0%,#1c2a48 30%,#1c2a48 70%,#a0532e 100%)" role="img" aria-label="Aerial view of solar panels on a roof"></div>
    <footer class="slide-footer"><span class="copy">(C) Copyright 2024 | All Rights Reserved</span><span class="page">Page 05 Of 08</span></footer>
  </section>

  <!-- Who we are -->
  <section class="slide col-a row-2">
    <h2 class="slide-title">Who We Are</h2><div class="title-rule"></div>
    <p class="body-text abs" style="left:44px;top:86px;width:354px">Sed ut perspiciatis unde omnis iste natus error sit voluptatem accusantium doloremque laudantium, totam rem aperiam, eaque ipsa quae ab illo inventore veritatis et quasi architecto beatae vitae dicta sunt explicabo. Nemo enim ipsam voluptatem quia voluptas sit</p>
    <div class="bullet" style="left:54px;top:183px;width:344px"><svg width="12" height="12" viewBox="0 0 12 12"><circle cx="6" cy="6" r="5" fill="none" stroke="var(--navy)" stroke-width="1.6"/><path d="M3.5 6h4M6 4l2 2-2 2" fill="none" stroke="var(--navy)" stroke-width="1.4"/></svg><span>Nemo enim ipsam voluptatem quia voluptas sit aspernatur aut odit aut fugit, sed quia consequuntur magni dolores eos qui ratione voluptatem sequi nesciunt.</span></div>
    <div class="bullet" style="left:54px;top:268px;width:344px"><svg width="12" height="12" viewBox="0 0 12 12"><circle cx="6" cy="6" r="5" fill="none" stroke="var(--navy)" stroke-width="1.6"/><path d="M3.5 6h4M6 4l2 2-2 2" fill="none" stroke="var(--navy)" stroke-width="1.4"/></svg><span>Neque porro quisquam est, qui dolorem ipsum quia dolor sit amet, consectetur, adipisci velit, sed quia non numquam eius modi tempora incidunt ut labore</span></div>
    <div class="bullet" style="left:54px;top:352px;width:344px"><svg width="12" height="12" viewBox="0 0 12 12"><circle cx="6" cy="6" r="5" fill="none" stroke="var(--navy)" stroke-width="1.6"/><path d="M3.5 6h4M6 4l2 2-2 2" fill="none" stroke="var(--navy)" stroke-width="1.4"/></svg><span>Ut enim ad minima veniam, quis nostrum exercitationem ullam corporis suscipit laboriosam, nisi ut aliquid ex ea commodi</span></div>
    <div class="photo round" style="left:447px;top:80px;width:290px;height:290px;background:linear-gradient(180deg,#5aa7e6 0%,#bfe0f7 50%,#3a6fb3 65%,#1b3768 100%);box-shadow:0 6px 16px rgba(0,0,0,.15)" role="img" aria-label="Wind turbines beside a solar panel field"></div>
    <svg class="abs" style="left:0;top:0" width="795" height="447"><circle cx="600" cy="224" r="146" fill="none" stroke="var(--magenta)" stroke-width="1.2"/></svg>
    <footer class="slide-footer"><span class="copy">(C) Copyright 2024 | All Rights Reserved</span><span class="page">Page 02 Of 08</span></footer>
  </section>

  <!-- Exit strategy -->
  <section class="slide col-b row-2">
    <h2 class="slide-title">Exit Strategy</h2><div class="title-rule"></div>
    <div class="bullet" style="left:45px;top:108px;width:350px;font-size:10.5px;line-height:23px;text-align:left"><svg width="10" height="10" viewBox="0 0 12 12"><circle cx="6" cy="6" r="6" fill="var(--magenta)"/><path d="M3 6h4.5M5.5 3.8 7.8 6 5.5 8.2" fill="none" stroke="#fff" stroke-width="1.5"/></svg><span>Funding rounds can be followed by Series A, B and C, more which can provide exit criteria for investors.</span></div>
    <div class="bullet" style="left:45px;top:178px;width:350px;font-size:10.5px;line-height:23px;text-align:left"><svg width="10" height="10" viewBox="0 0 12 12"><circle cx="6" cy="6" r="6" fill="var(--magenta)"/><path d="M3 6h4.5M5.5 3.8 7.8 6 5.5 8.2" fill="none" stroke="#fff" stroke-width="1.5"/></svg><span>Management Buyout or Merger with a competitor or Acquisition by a Bigger Corporation.</span></div>
    <div class="bullet" style="left:45px;top:247px;width:350px;font-size:10.5px;line-height:23px;text-align:left"><svg width="10" height="10" viewBox="0 0 12 12"><circle cx="6" cy="6" r="6" fill="var(--magenta)"/><path d="M3 6h4.5M5.5 3.8 7.8 6 5.5 8.2" fill="none" stroke="#fff" stroke-width="1.5"/></svg><span>Building a public-ready Company 8-10 years with 20x ROI.</span></div>
    <div class="step" style="top:93px"><span class="dot" style="background:var(--magenta)"><svg width="30" height="30" viewBox="0 0 30 30" fill="none" stroke="#fff" stroke-width="1.4"><path d="M4 18l7-6 5 4 9-9M21 7h4v4"/><rect x="5" y="21" width="6" height="5"/><rect x="13" y="20" width="6" height="6"/><rect x="21" y="19" width="5" height="7"/></svg></span><b>STEP 01:</b><em>Initial Public Offering (IPO)</em></div>
    <div class="step" style="top:184px"><span class="dot" style="background:var(--navy)"><svg width="30" height="30" viewBox="0 0 30 30" fill="none" stroke="#fff" stroke-width="1.4"><circle cx="15" cy="9" r="4"/><path d="M5 22l6-5 4 3 4-3 6 5M9 25l3-2M21 25l-3-2"/></svg></span><b>STEP 02:</b><em>Merger or Acquisition (M&amp;A)</em></div>
    <div class="step" style="top:275px"><span class="dot" style="background:var(--blue)"><svg width="30" height="30" viewBox="0 0 30 30" fill="none" stroke="#fff" stroke-width="1.4"><circle cx="15" cy="15" r="10"/><circle cx="15" cy="15" r="5"/><path d="M15 12v6M13 14h4"/></svg></span><b>STEP 03:</b><em>Further Funding Rounds</em></div>
    <footer class="slide-footer"><span class="copy">(C) Copyright 2024 | All Rights Reserved</span><span class="page">Page 06 Of 08</span></footer>
  </section>

  <!-- Services -->
  <section class="slide col-a row-3">
    <h2 class="slide-title">Services We Provide</h2><div class="title-rule"></div>
    <svg class="abs" style="left:0;top:0" width="795" height="447"><circle cx="265" cy="245" r="150" fill="none" stroke="var(--magenta)" stroke-width="1"/></svg>
    <div class="abs round" style="left:78px;top:118px;width:260px;height:260px;background:var(--navy);display:flex;align-items:center;justify-content:center"><span style="font-family:'Jost',sans-serif;font-weight:600;font-size:72px;color:var(--white)">K7V</span></div>
    <div class="icon-dot" style="left:306px;top:92px;background:var(--orange)"><svg width="30" height="30" viewBox="0 0 30 30" fill="none" stroke="#fff" stroke-width="1.5"><path d="M11 19a7 7 0 1 1 8 0v3h-8z"/><path d="M12 25h6M15 2v2M4 13h2M24 13h2M7 6l1.5 1.5M23 6l-1.5 1.5"/></svg></div>
    <div class="icon-dot" style="left:370px;top:168px;background:var(--blue)"><svg width="30" height="30" viewBox="0 0 30 30" fill="none" stroke="#fff" stroke-width="1.5"><rect x="9" y="4" width="16" height="22" rx="2"/><rect x="12" y="7" width="10" height="4"/><path d="M12 15h2M16 15h2M20 15h2M12 19h2M16 19h2M20 19h2"/><ellipse cx="7" cy="20" rx="4" ry="1.5"/><ellipse cx="7" cy="24" rx="4" ry="1.5"/></svg></div>
    <div class="icon-dot" style="left:369px;top:257px;background:var(--yellow)"><svg width="30" height="30" viewBox="0 0 30 30" fill="none" stroke="#fff" stroke-width="1.5"><circle cx="10" cy="9" r="3"/><path d="M10 2v2M3 9h2M5 4l1.5 1.5"/><path d="M13 14h14l-3 8H10z M15 14l-2 8M19 14l-2 8M23 14l-2 8M11 18h15"/><path d="M4 26v-4h4v4"/></svg></div>
    <div class="icon-dot" style="left:309px;top:339px;background:var(--teal)"><svg width="30" height="30" viewBox="0 0 30 30" fill="none" stroke="#fff" stroke-width="1.6"><path d="M6 24L20 10M18 6a5 5 0 0 0 6 6l-3-3zM24 24L10 10M6 6l4 4"/></svg></div>
    <div class="service" style="left:400px;top:92px"><h3>EPC SOLUTIONS</h3><p>Get turnkey EPC solutions that cover engineering,<br>procurement, and construction.</p></div>
    <div class="service" style="left:463px;top:167px"><h3>SOLAR FINANCING</h3><p>Maintenance With our assistance, you can finance the installation of solar panels &amp; renewable energy.</p></div>
    <div class="service" style="left:462px;top:256px"><h3>INSTALLATION AND COMMISSION</h3><p>With our 24/7 remote monitoring, you may install and run solar panels without worrying about performance issues.</p></div>
    <div class="service" style="left:402px;top:338px"><h3>OPERATION AND MAINTENANCE</h3><p>Get expert advice on how to run the solar plant once it has<br>been installed.</p></div>
    <footer class="slide-footer"><span class="copy">(C) Copyright 2024 | All Rights Reserved</span><span class="page">Page 03 Of 08</span></footer>
  </section>

  <!-- Company introductions -->
  <section class="slide col-b row-3">
    <h2 class="slide-title">Company Introductions</h2><div class="title-rule"></div>
    <div class="abs" style="left:44px;top:86px;width:355px">
      <p class="body-text">Company Name was established to mitigate reliance on finite resources. We offer consultancy, services, and products promoting the adoption of Solar Power—a potent renewable energy source.</p>
      <h3 class="sub-head">OUR VISION:</h3>
      <p class="body-text">Our Vision is to transform India into an environmentally sustainable nation, characterized by clean and green practices that center around renewable energy adoption</p>
      <h3 class="sub-head">OUR VALUES:</h3>
      <p class="body-text"><span class="strong">UNMATCHED QUALITY:</span> With several intense quality control protocols and stringent procedures, we ensure that all our products have the highest quality.</p>
      <p class="body-text" style="margin-top:8px"><span class="strong">UTMOST SATISFACTION:</span> Guided by unwavering professionalism and accountability.</p>
    </div>
    <div class="photo round" style="left:446px;top:90px;width:290px;height:290px;background:linear-gradient(180deg,#e6d26a 0%,#9bb04a 35%,#5a7d33 55%,#2a3f6e 75%,#1b2a4c 100%);box-shadow:0 6px 16px rgba(0,0,0,.15)" role="img" aria-label="Sunlit valley with a solar farm in the foreground"></div>
    <svg class="abs" style="left:0;top:0" width="795" height="447"><circle cx="604" cy="231" r="148" fill="none" stroke="var(--magenta)" stroke-width="1.2"/></svg>
    <footer class="slide-footer"><span class="copy">(C) Copyright 2024 | All Rights Reserved</span><span class="page">Page 07 Of 08</span></footer>
  </section>

  <!-- Competitive advantage -->
  <section class="slide col-a row-4">
    <h2 class="slide-title">Competitive Advantage</h2><div class="title-rule"></div>
    <div class="adv" style="left:70px;top:129px">
      <div class="ring" style="border:1.5px solid var(--navy)"><span><svg width="46" height="46" viewBox="0 0 46 46"><path d="M23 3l5 4 6-1 2 6 5 3-2 6 2 6-5 3-2 6-6-1-5 4-5-4-6 1-2-6-5-3 2-6-2-6 5-3 2-6 6 1z" fill="var(--navy)"/><circle cx="23" cy="23" r="11" fill="none" stroke="#fff" stroke-width="2"/><path d="M18 23l4 4 6-7" fill="none" stroke="#fff" stroke-width="2.4"/></svg></span></div>
      <h3 style="color:var(--navy)">FOCUS ON QUALITY</h3>
      <p>Our stringent quality control methods enable us to provide high-quality products that we provide warranties upto 25 years.</p>
    </div>
    <div class="adv" style="left:297px;top:129px">
      <div class="ring" style="border:1.5px solid var(--blue)"><span><svg width="46" height="46" viewBox="0 0 46 46"><path d="M10 22l14-10 14 10v16H10z" fill="var(--blue)"/><rect x="20" y="28" width="7" height="10" fill="#fff"/><path d="M6 18l10-8 14 3-10 8z" fill="#26415a"/><path d="M10 16l10 3M13 13l10 3" stroke="#fff" stroke-width=".8"/><circle cx="34" cy="8" r="4" fill="var(--blue)"/></svg></span></div>
      <h3 style="color:var(--blue)">STATE OF THE ART TECHNOLOGY</h3>
      <p>Our access to advanced technology lets us create cutting-edge solar solutions that adapt flexibly to suit specific requirements.</p>
    </div>
    <div class="adv" style="left:524px;top:129px">
      <div class="ring" style="border:1.5px solid var(--teal)"><span><svg width="46" height="46" viewBox="0 0 46 46"><path d="M8 22h18l6 10H14z" fill="var(--teal)"/><path d="M14 22l6 10M20 22l6 10M11 27h19" stroke="#fff" stroke-width="1"/><circle cx="30" cy="18" r="5" fill="var(--yellow)"/><path d="M30 8v3M38 18h3M36 11l2-2M22 11l2 2" stroke="var(--yellow)" stroke-width="1.5"/></svg></span></div>
      <h3 style="color:var(--teal)">UNRIVALLED EXPERIENCE</h3>
      <p>We have worked on 2500+ projects with a diverse client base while maintaining consistent quality.&nbsp; Experience and Technology enable us</p>
    </div>
    <footer class="slide-footer"><span class="copy">(C) Copyright 2024 | All Rights Reserved</span><span class="page">Page 04 Of 08</span></footer>
  </section>

  <!-- Fund raise -->
  <section class="slide col-b row-4">
    <h2 class="slide-title">Fund Raise</h2><div class="title-rule"></div>
    <div class="abs" style="left:44px;top:98px;width:330px">
      <h3 class="sub-head" style="margin:0 0 10px">COMPANY NAME ENERGY IS RAISING:</h3>
      <p class="body-text" style="text-align:left">Total Funding – ₹122Cr INR ($14.5 Mn) to build and start operations of a solar panel manufacturing plant in India.</p>
      <p class="body-text" style="text-align:left;margin-top:16px">We are looking to raise capital in a 65% Equity and 35% Debt ratio.</p>
    </div>
    <svg class="abs" style="left:0;top:0" width="795" height="447" viewBox="0 0 795 447" role="img" aria-label="Funding allocation chart">
      <path d="M575 207 L575 39 A168 168 0 0 1 743 207 Z" fill="var(--orange)"/>
      <path d="M575 207 L753 207 A178 178 0 0 1 575 385 Z" fill="var(--yellow)"/>
      <path d="M575 207 L575 371 A164 164 0 0 1 459 91 Z" fill="var(--blue)"/>
      <path d="M575 207 L485 117 A127 127 0 0 1 575 80 Z" fill="var(--magenta)"/>
      <circle cx="575" cy="207" r="75" fill="var(--navy)"/>
      <circle cx="575" cy="207" r="51" fill="var(--white)"/>
      <text x="575" y="217" text-anchor="middle" font-family="Jost, sans-serif" font-weight="600" font-size="28" fill="var(--orange)">K7V</text>
      <text class="chart-label" x="546" y="109" font-size="8" text-anchor="middle">Payroll</text>
      <text class="chart-label" x="534" y="133" font-size="15" text-anchor="middle">02%</text>
      <text class="chart-label" x="665" y="144" font-size="11" text-anchor="middle">Startup Expenses</text>
      <text class="chart-label" x="690" y="176" font-size="19" text-anchor="middle">02%</text>
      <text class="chart-label" x="692" y="254" font-size="19" text-anchor="middle">38%</text>
      <text class="chart-label" x="692" y="272" font-size="11" text-anchor="middle">CAPEX</text>
      <text class="chart-label" x="462" y="239" font-size="19" text-anchor="middle">58%</text>
      <text class="chart-label" x="502" y="301" font-size="11" text-anchor="middle">Working Capital</text>
    </svg>
    <footer class="slide-footer"><span class="copy">(C) Copyright 2024 | All Rights Reserved</span><span class="page">Page 08 Of 08</span></footer>
  </section>

</div>
</body>
</html>
```